Logo, Web and Mobile Designs for enterprise social media platform

All the details are in the attached document, please start reading the scope document first which explains what is this project about and the details about the needed deliverables, after that please read the UI_Requirements document which will detail what is expected regarding the coded web version since this is a coded contest, it is very important that you meet the UI requirements or suggest something else but we will need to agree first before working on the coded version

Good Luck

Target Market(s)

Enterprise Social Media

Industry/Entity Type

Media

Coding

Coded - Design and coding required

Number of Pages Required

5+ page

Font styles to use
Sans Serif

Requirements
Must have
• All the must haves are listed in the scope document so please check before you start

```html
<!DOCTYPE html>
<html lang="en">
<head>
<meta charset="utf-8">
<title>Teamora – Social Media Platform</title>
<link rel="stylesheet" href="https://fonts.googleapis.com/css2?family=Open+Sans:wght@400;600;700&display=swap">
<style>
  :root {
    --green: #7dc142;
    --teal: #29a4ac;
    --teal-light: #4fbac0;
    --header-dark: #1f2220;
    --footer-dark: #262626;
    --white: #ffffff;
    --muted: #d8d8d8;
  }
  * { margin: 0; padding: 0; box-sizing: border-box; }
  html, body { width: 1200px; height: 666px; overflow: hidden; }
  body { font-family: "Open Sans", Arial, sans-serif; color: var(--white); background: var(--teal); position: relative; }

  .site-header {
    position: absolute; left: 0; top: 0; width: 1200px; height: 75px;
    border-top: 3px solid var(--green);
  }
  .header-backdrop {
    position: absolute; inset: 0;
    background: linear-gradient(90deg, #151816 0%, #2a2c25 45%, #3a3a2e 70%, #1c1f1d 100%);
  }
  .brand {
    position: absolute; left: 162px; top: 20px;
    display: flex; align-items: center; gap: 8px;
    font-weight: 700; font-size: 27px; letter-spacing: 0.5px; color: var(--white);
  }
  .brand-dot { width: 14px; height: 14px; border-radius: 50%; background: var(--green); }
  .main-nav { position: absolute; top: 0; left: 0; height: 72px; width: 100%; }
  .main-nav a {
    position: absolute; top: 32px; font-size: 11px; font-weight: 600;
    color: var(--white); text-decoration: none; letter-spacing: 0.2px;
  }
  .main-nav a.is-active { color: var(--green); }
  .login-button {
    position: absolute; left: 959px; top: 20px; width: 78px; height: 35px;
    background: var(--green); color: var(--white); font-size: 12px; font-weight: 600;
    display: flex; align-items: center; justify-content: center; gap: 4px; border-radius: 2px;
  }

  .hero { position: absolute; left: 0; top: 75px; width: 1200px; height: 525px; background: var(--teal); }
  .hero-title {
    position: absolute; left: 162px; top: 137px; width: 420px;
    font-size: 41px; line-height: 45px; font-weight: 700;
  }
  .hero-lead {
    position: absolute; left: 164px; top: 240px; width: 400px;
    font-size: 17.5px; line-height: 28px; font-weight: 400;
  }
  .hero-lead strong { font-weight: 700; }
  .read-more {
    position: absolute; left: 163px; top: 325px; width: 163px; height: 35px;
    background: var(--green); color: var(--white); font-size: 12px; font-weight: 600;
    display: flex; align-items: center; padding-left: 13px; gap: 10px; border-radius: 2px;
  }
  .slider-dots { position: absolute; left: 163px; top: 458px; display: flex; gap: 9px; }
  .slider-dots span { width: 22px; height: 4px; background: var(--white); }
  .slider-dots span.is-current { background: var(--green); }
  .hero-illustration {
    position: absolute; left: 612px; top: 53px; width: 530px; height: 472px;
    background: linear-gradient(180deg, rgba(79,186,192,0.35) 0%, rgba(40,120,150,0.45) 100%);
    border-radius: 4px;
  }

  .site-footer { position: absolute; left: 0; top: 600px; width: 1200px; height: 66px; background: var(--footer-dark); }
  .copyright { position: absolute; left: 161px; top: 24px; font-size: 11.5px; color: var(--muted); }
  .social-links { position: absolute; left: 863px; top: 18px; display: flex; gap: 5px; }
  .social-links span { width: 31px; height: 31px; border: 1.5px solid var(--muted); border-radius: 50%; }
</style>
</head>
<body>
  <header class="site-header">
    <div class="header-backdrop" role="img" aria-label="Dimmed office photo with a plant on a desk"></div>
    <div class="brand"><span>TEAMORA</span><span class="brand-dot"></span></div>
    <nav class="main-nav">
      <a class="is-active" style="left:542px">HOME</a>
      <a style="left:612px">ABOUT US</a>
      <a style="left:702px">SERVICES</a>
      <a style="left:787px">PRODUCTS</a>
      <a style="left:880px">CONTACT</a>
    </nav>
    <div class="login-button">
      <svg width="8" height="10" viewBox="0 0 8 10" aria-hidden="true">
        <path d="M2 4V3a2 2 0 0 1 4 0v1" fill="none" stroke="#fff" stroke-width="1.3"/>
        <rect x="0.5" y="4" width="7" height="6" rx="1" fill="#fff"/>
      </svg>
      LOGIN
    </div>
  </header>

  <section class="hero">
    <h1 class="hero-title">Teamora is Social Media Platform</h1>
    <p class="hero-lead">Join the 10+ million professionals who trust Teamora. <strong>GET STARTED FOR FREE.</strong></p>
    <div class="read-more">
      <svg width="17" height="11" viewBox="0 0 17 11" aria-hidden="true">
        <path d="M0 0l8 5.5L0 11z M8 0l8 5.5L8 11z" fill="#fff"/>
      </svg>
      READ MORE HERE
    </div>
    <div class="slider-dots"><span class="is-current"></span><span></span><span></span><span></span></div>
    <div class="hero-illustration" role="img" aria-label="Illustration of raised hands holding megaphones, a phone, a globe, a video player, an envelope and a chat bubble"></div>
  </section>

  <footer class="site-footer">
    <p class="copyright">© 2015 Teamora. All right reserved&nbsp; Term of Use</p>
    <div class="social-links"><span></span><span></span><span></span><span></span><span></span></div>
  </footer>
</body>
</html>
```